Business Card Design For A Renovation Contractor Company

We need a business card for a new company based in Singapore, our company name is "RB Tolvane". We are a renovation contractor that builds designs into reality. We build more of F&B restaurants, retail stores and commercial offices. We work very closely with designers. The final design should communicate to our client that we are a company that you can trust, that will plan and complete your project without giving you a headache. I like my client to remember my company as "RB". The beauty of SIMPLE is important.

Industry/Entity Type

Contractor

Requirements
Nice to have
• Black or Red base

```html
<!DOCTYPE html>
<html lang="en">
<head>
<meta charset="utf-8">
<title>RB Tolvane — Business Card</title>
<link href="https://fonts.googleapis.com/css2?family=Arimo:wght@400;700&family=Questrial&display=swap" rel="stylesheet">
<style>
  :root {
    --page: #e9e7e4;
    --card-white: #ffffff;
    --ink: #2b2b2b;
    --ink-soft: #555555;
    --brand-red: #e3141f;
    --card-black: #0b0b0b;
    --rule: #d9d9d9;
  }
  * { box-sizing: border-box; margin: 0; padding: 0; }
  html, body { width: 1200px; height: 720px; overflow: hidden; }
  body {
    background: var(--page);
    font-family: "Arimo", Arial, sans-serif;
    color: var(--ink);
    position: relative;
  }
  .card {
    position: absolute;
    top: 205px;
    width: 540px;
    height: 309px;
    overflow: hidden;
    box-shadow: 0 6px 18px rgba(0,0,0,0.18);
  }

  /* Front */
  .card-front { left: 40px; background: var(--card-white); }
  .front-brand {
    position: absolute;
    left: 40px; top: 96px;
    width: 250px;
    text-align: center;
  }
  .brand-mark {
    display: flex; align-items: center; justify-content: center; gap: 10px;
  }
  .brand-dot {
    width: 30px; height: 30px; border-radius: 50%;
    background: var(--brand-red);
    flex: none;
  }
  .brand-name {
    font-size: 34px; font-weight: 400; color: var(--ink);
    letter-spacing: 0.5px; white-space: nowrap;
  }
  .brand-tagline {
    margin-top: 6px;
    padding-top: 4px;
    border-top: 1px solid var(--ink);
    font-size: 15px;
    color: var(--ink);
    letter-spacing: 0.3px;
    white-space: nowrap;
  }
  .front-divider {
    position: absolute;
    left: 318px; top: 26px;
    width: 1px; height: 160px;
    background: var(--rule);
  }
  .contact {
    position: absolute;
    left: 334px; top: 28px;
  }
  .contact-name {
    font-size: 18px; font-weight: 700; color: var(--brand-red);
  }
  .contact-title { font-size: 12px; color: var(--ink); margin-bottom: 10px; }
  .contact-line {
    display: flex; align-items: center; gap: 6px;
    font-size: 13px; color: var(--ink-soft); line-height: 17px;
  }
  .contact-line svg { width: 10px; height: 10px; fill: var(--brand-red); flex: none; }
  .contact-address {
    margin-top: 12px;
    font-size: 12.5px; color: var(--ink-soft); line-height: 16px;
  }
  .front-band-black {
    position: absolute;
    left: 0; bottom: 0;
    width: 100%; height: 20px;
    background: var(--card-black);
  }
  .front-band-red {
    position: absolute;
    right: 0; bottom: 20px;
    width: 220px; height: 36px;
    background: var(--brand-red);
    clip-path: polygon(14px 0, 100% 0, 100% 100%, 0 100%);
    display: flex; align-items: center; justify-content: center;
  }
  .front-url {
    font-family: "Questrial", Arial, sans-serif;
    color: #ffffff; font-size: 13px; letter-spacing: 2.5px;
  }

  /* Back */
  .card-back {
    left: 620px;
    background: var(--card-black);
    color: #ffffff;
  }
  .back-brand {
    position: absolute;
    left: 0; right: 0; top: 88px;
    display: flex; align-items: center; justify-content: center; gap: 18px;
  }
  .back-ring {
    width: 70px; height: 70px; border-radius: 50%;
    border: 10px solid #ffffff;
    flex: none;
  }
  .back-name {
    font-size: 44px; font-weight: 400; letter-spacing: 1px; white-space: nowrap;
  }
  .back-url {
    position: absolute;
    left: 0; right: 0; bottom: 52px;
    text-align: center;
    font-family: "Questrial", Arial, sans-serif;
    font-size: 20px; letter-spacing: 3px;
  }
</style>
</head>
<body>

<section class="card card-front">
  <div class="front-brand">
    <div class="brand-mark">
      <span class="brand-dot"></span>
      <span class="brand-name">RB Tolvane</span>
    </div>
    <p class="brand-tagline">plans made into real spaces</p>
  </div>

  <div class="front-divider"></div>

  <div class="contact">
    <p class="contact-name">Your Name</p>
    <p class="contact-title">Title</p>
    <p class="contact-line">
      <svg viewBox="0 0 10 10"><path d="M2 0.5 L3.8 2.6 L2.9 3.7 Q4 6 6.3 7.1 L7.4 6.2 L9.5 8 L8.2 9.5 Q3.5 9 0.5 1.8 Z"/></svg>
      123-456-7890
    </p>
    <p class="contact-line">
      <svg viewBox="0 0 10 10"><rect x="2.5" y="0.5" width="5" height="9" rx="1"/></svg>
      456-085-4321
    </p>
    <p class="contact-line">
      <svg viewBox="0 0 10 10"><path d="M0.5 2 H9.5 V8.5 H0.5 Z M0.5 2 L5 5.5 L9.5 2" stroke="#fff" stroke-width="0.8"/></svg>
      info@rbtolvane.com
    </p>
    <p class="contact-address">Door No. Street Name<br>City Name, State, Zip Code.</p>
  </div>

  <div class="front-band-red"><span class="front-url">www.rbtolvane.com</span></div>
  <div class="front-band-black"></div>
</section>

<section class="card card-back">
  <div class="back-brand">
    <span class="back-ring"></span>
    <span class="back-name">RB Tolvane</span>
  </div>
  <p class="back-url">www.rbtolvane.com</p>
</section>

</body>
</html>
```